Animal Eye Clinic needs a Business card

We are a new veterinary ophthalmology practice (Ridgeline Pet Vision Care) and we need a business card designed. We only see animal eyes - we are not a regular veterinary clinic. We already have a logo. We are looking for a professional, good looking business card to hand out to our clients. We are looking for something simple but professional and contemporary. Our logo is likely the only picture/graphic that needs to be on the card.
Updates

Contact Information for Business Card

Delia Vossman, BSc, DVM, MSc, DipACVO
Veterinary Ophthalmologist

Phone: 250.418.3927
Email: ridgelinepetvisioncare@mailbox-example.net
Website: ridgelinepetvisioncare-example.net
Address: 1874 Thornbury Rd
Kelowna, BC, V1X 4M9

Colors

Designer to choose colors to be used in the design.

Requirements
Must have
• Our logo (attached)

```html
<!DOCTYPE html>
<html lang="en">
<head>
<meta charset="utf-8">
<title>Ridgeline Pet Vision Care – Business Card</title>
<link rel="stylesheet" href="https://fonts.googleapis.com/css2?family=Roboto:wght@400;700&display=swap">
<style>
  :root {
    --teal: #1b98a8;
    --white: #ffffff;
    --ink: #5a5a5a;
    --rule: #8a8a8a;
    --bg-top: #e4e6e8;
    --bg-bottom: #b9bcbf;
  }
  * { margin: 0; padding: 0; box-sizing: border-box; }
  html, body { width: 1200px; height: 800px; overflow: hidden; }
  body {
    background: linear-gradient(160deg, var(--bg-top), var(--bg-bottom));
    font-family: "Roboto", Arial, sans-serif;
    position: relative;
  }
  .card {
    position: absolute;
    width: 560px;
    height: 320px;
    box-shadow: 0 6px 18px rgba(0,0,0,0.25);
  }
  /* Front side */
  .card--front {
    left: 570px; top: 60px;
    background: var(--teal);
    display: flex; align-items: center; justify-content: center; gap: 22px;
  }
  .brand-dot {
    width: 74px; height: 74px; border-radius: 50%;
    background: var(--white); flex: none;
  }
  .brand-name {
    color: var(--white);
    font-weight: 700;
    font-size: 30px;
    line-height: 1.15;
    text-transform: uppercase;
    letter-spacing: 0.5px;
  }
  /* Back side */
  .card--back {
    left: 70px; top: 410px;
    background: var(--white);
    color: var(--ink);
  }
  .back-brand {
    position: absolute; right: 34px; top: 30px;
    display: flex; align-items: center; gap: 12px;
  }
  .back-brand .brand-dot { width: 38px; height: 38px; background: var(--teal); }
  .back-brand .brand-name { color: var(--teal); font-size: 19px; }
  .person { position: absolute; left: 40px; top: 108px; }
  .person-name { color: var(--teal); font-weight: 700; font-size: 21px; text-transform: uppercase; }
  .person-creds { font-size: 14px; text-transform: none; }
  .person-title { font-size: 16px; margin-top: 2px; }
  .contact { position: absolute; left: 40px; top: 184px; list-style: none; font-size: 14.5px; }
  .contact li { display: flex; align-items: center; gap: 8px; line-height: 21px; }
  .contact svg { width: 13px; height: 13px; flex: none; }
  .rule {
    position: absolute; left: 40px; right: 40px; top: 250px;
    border-top: 1px solid var(--rule);
  }
  .address {
    position: absolute; right: 40px; top: 262px;
    font-style: normal; text-align: right; font-size: 16px; line-height: 20px;
  }
</style>
</head>
<body>
  <section class="card card--front">
    <span class="brand-dot"></span>
    <div class="brand-name">Ridgeline Pet<br>Vision Care</div>
  </section>

  <section class="card card--back">
    <div class="back-brand">
      <span class="brand-dot"></span>
      <div class="brand-name">Ridgeline Pet<br>Vision Care</div>
    </div>

    <div class="person">
      <div class="person-name">Delia Vossman<span class="person-creds">, BSc, DVM, MSc, DipACVO</span></div>
      <div class="person-title">Veterinary Ophthalmologist</div>
    </div>

    <ul class="contact">
      <li>
        <svg viewBox="0 0 16 16" aria-hidden="true"><path fill="var(--teal)" d="M3.6 1.2l2.3 2.6-1.2 1.9c.9 2 2.6 3.7 4.6 4.6l1.9-1.2 2.6 2.3-1.3 2.4C7.3 13.6 2.4 8.7 1.2 3.5z"/></svg>
        250.418.3927
      </li>
      <li>
        <svg viewBox="0 0 16 16" aria-hidden="true"><rect x="1" y="3" width="14" height="10" fill="none" stroke="var(--teal)" stroke-width="1.6"/><path d="M1 3l7 6 7-6" fill="none" stroke="var(--teal)" stroke-width="1.6"/></svg>
        ridgelinepetvisioncare@mailbox-example.net
      </li>
      <li>
        <svg viewBox="0 0 16 16" aria-hidden="true"><g fill="none" stroke="var(--teal)" stroke-width="1.3"><circle cx="8" cy="8" r="6.5"/><ellipse cx="8" cy="8" rx="2.8" ry="6.5"/><path d="M1.5 8h13M2.5 4.8h11M2.5 11.2h11"/></g></svg>
        ridgelinepetvisioncare-example.net
      </li>
    </ul>

    <div class="rule"></div>

    <address class="address">
      1874 Thornbury Rd<br>
      Kelowna, BC, V1X 4M9
    </address>
  </section>
</body>
</html>
```